Modern Verdell Tree Care Website

I need a website for a full service Tree Care company. The company provides tree pruning, tree removal, tree preservation, emergency services, stump grinding, and emergency tree services.

Target Market(s)

Customers that need tree services

Industry/Entity Type

Landscaping, Tree Services

Coding

Coded - Design and coding required

Number of Pages Required

5+ page

Font styles to use
Sans Serif

Requirements
Must have
• Good clean design that showcases the services the company provides.
Nice to have
• Services page; contact form, blog, home page, about page

```html
<!DOCTYPE html>
<html lang="en">
<head>
<meta charset="utf-8">
<title>Verdell Tree Care</title>
<link href="https://fonts.googleapis.com/css2?family=Poppins:wght@300;400;500;600;700;800&display=swap" rel="stylesheet">
<style>
:root{
  --green:#28b93a;
  --forest:#2e4a20;
  --sage:#e8eee1;
  --orange:#f07a22;
  --amber:#f6a53a;
  --blue:#2a8cf0;
  --ink:#2b2b2b;
  --muted:#6a6a6a;
  --white:#ffffff;
  --stage:#000000;
}
*{margin:0;padding:0;box-sizing:border-box}
html,body{width:1200px;height:1200px;overflow:hidden;background:var(--stage);font-family:'Poppins',sans-serif;color:var(--ink)}
.stage{position:absolute;left:0;top:0;width:1932px;height:1932px;transform:scale(0.621118);transform-origin:0 0}
.page{position:absolute;left:691px;top:0;width:550px;height:1932px;background:var(--white);overflow:hidden}
.abs{position:absolute}
.photo{position:absolute}
/* hero */
.hero{left:0;top:0;width:550px;height:281px;background:linear-gradient(180deg,#9fc24a 0%,#3f6a1c 35%,#2c5113 65%,#507a1d 100%)}
.hero-glow{left:0;top:0;width:550px;height:281px;background:radial-gradient(circle at 53% 8%,rgba(255,245,170,.75),rgba(255,245,170,0) 45%)}
.nav{left:57px;top:25px;width:437px;height:24px;background:var(--white)}
.brand{position:absolute;left:4px;top:2px;display:flex;align-items:center;gap:3px}
.brand-mark{width:18px;height:18px;background:var(--green)}
.brand-name{font-weight:700;font-size:10px;line-height:10px;color:var(--forest);letter-spacing:.5px}
.brand-name small{display:block;font-size:6px;line-height:8px;font-weight:700;color:var(--forest);letter-spacing:1.5px}
.nav-links{position:absolute;top:9px;font-size:4.5px;color:var(--muted)}
.nav-cta{position:absolute;left:359px;top:0;width:78px;height:24px;background:var(--amber);font-size:5px;font-weight:600;color:var(--ink);display:flex;align-items:center;justify-content:center}
.hero-title{left:0;width:550px;top:123px;text-align:center;color:var(--white);font-weight:700;font-size:17px;line-height:22px;letter-spacing:.3px}
.hero-title .accent{color:var(--orange)}
.hero-sub{left:0;width:550px;top:166px;text-align:center;color:var(--white);font-size:6.5px;font-weight:600;letter-spacing:2.6px}
/* who we are */
.who{left:56px;top:243px;width:439px;height:334px;background:var(--sage)}
.h-who{left:46px;top:15px;font-size:17px;font-weight:700;color:var(--forest)}
.who-text{left:46px;top:37px;width:176px;font-size:4.4px;line-height:6.4px;color:var(--ink);text-align:justify}
.who-text p+p{margin-top:6px}
.estimate{right:46px;top:44px;text-align:right}
.estimate .lead{font-size:5px;font-weight:600;color:var(--forest)}
.estimate .phone{font-size:13px;font-weight:600;color:var(--orange);line-height:15px}
.who-rule{left:46px;top:96px;width:347px;height:1px;background:#cdd6c4}
.h-do{left:46px;top:115px;font-size:7.5px;font-weight:600;color:var(--forest)}
.svc{top:135px;width:109px}
.svc .img{width:109px;height:63px}
.svc h3{margin-top:9px;font-size:5.8px;font-weight:700;color:var(--forest);letter-spacing:.2px}
.svc p{margin-top:2px;width:70px;font-size:3.4px;line-height:4.6px;color:var(--ink)}
.svc .more{display:inline-block;margin-top:4px;font-size:3.6px;font-weight:600;border-bottom:1px solid var(--ink);padding-bottom:2px}
.perks{left:0;top:277px;width:439px;height:57px;background:var(--green)}
.perk{top:19px;display:flex;align-items:center;gap:4px;color:var(--white)}
.perk b{display:block;font-size:4px;font-weight:600}
.perk span{display:block;font-size:3.4px;opacity:.9;margin-top:2px}
/* expertise */
.kicker{left:102px;top:621px;font-size:3.8px;color:var(--muted)}
.kicker-dash{left:102px;top:629px;width:4px;height:1px;background:var(--ink)}
.h-exp{left:102px;top:637px;width:165px;font-size:8.4px;line-height:11px;font-weight:600;color:var(--ink)}
.h-exp em{font-style:normal;color:var(--green)}
.checks{left:102px;top:681px;font-size:4px;color:var(--muted);list-style:none}
.checks li{display:flex;align-items:center;gap:3px;height:9px}
.video{left:280px;top:612px;width:169px;height:99px;background:linear-gradient(180deg,#9aa4ad 0%,#6a6f6a 40%,#3f5a2a 70%,#2d3a28 100%)}
.play{position:absolute;left:75px;top:42px;width:15px;height:15px;border-radius:50%;background:var(--green)}
/* services */
.svc-hero{left:102px;top:750px;width:169px;height:169px;background:linear-gradient(160deg,#6a8a3a 0%,#4f7a2a 45%,#2e4a1f 100%)}
.svc-hero .label{position:absolute;left:0;width:169px;top:65px;text-align:center;color:var(--white);font-size:21px;font-weight:800}
.svc-hero .sub{position:absolute;left:0;width:169px;top:96px;text-align:center;color:var(--white);font-size:4px;font-weight:600}
.tile{width:78px;height:77px;background:var(--sage);display:flex;flex-direction:column;align-items:center;justify-content:center;gap:6px}
.tile span{font-size:4px;font-weight:600;color:var(--muted)}
/* recent work */
.work-band{left:0;top:959px;width:550px;height:172px;background:var(--green)}
.h-work{left:102px;top:996px;width:170px;font-size:16.5px;line-height:21px;font-weight:700;color:var(--white)}
.work-text{left:281px;top:996px;width:168px;font-size:4.1px;line-height:8.4px;color:var(--white)}
.before{left:102px;top:1057px;width:174px;height:185px;background:linear-gradient(180deg,#5a6a3a 0%,#4a6d2a 35%,#3d5a22 100%)}
.after{left:276px;top:1057px;width:173px;height:185px;background:linear-gradient(180deg,#6a9a3a 0%,#b85c6a 40%,#6fa63c 65%,#8a90b0 100%)}
.slider{left:270px;top:1143px;width:12px;height:12px;border-radius:50%;background:var(--white);font-size:5px;display:flex;align-items:center;justify-content:center;color:var(--ink)}
.thumb{width:80px;height:80px}
.projects{left:281px;top:1279px;width:168px;height:167px;background:linear-gradient(180deg,#6f8fb0 0%,#9fb0be 35%,#3d4a35 65%,#2a3a1e 100%)}
.projects .label{position:absolute;left:0;width:168px;top:64px;text-align:center;color:var(--white);font-size:20px;font-weight:800}
.projects .sub{position:absolute;left:0;width:168px;top:94px;text-align:center;color:var(--white);font-size:4px;font-weight:600}
/* estimate form */
.quote{left:0;top:1487px;width:317px;height:245px;background:var(--green)}
.quote-photo{left:317px;top:1487px;width:233px;height:245px;background:linear-gradient(160deg,#f2b04a 0%,#c88a3a 30%,#6a8a3a 60%,#3a5a22 100%)}
.h-quote{left:102px;top:1533px;font-size:16px;font-weight:700;color:var(--white)}
.form-label{top:1573px;font-size:5px;font-weight:600;color:var(--white)}
.field{left:102px;width:125px;height:11px;background:var(--white);font-size:3.6px;color:#aaa;padding:3px 3px}
.opt{left:236px;display:flex;align-items:center;gap:4px;font-size:4px;color:var(--white)}
.opt i{width:6px;height:6px;background:var(--white)}
.submit{left:102px;top:1668px;width:55px;height:16px;background:var(--blue);color:var(--white);font-size:3.8px;display:flex;align-items:center;justify-content:center}
/* footer */
.footer{left:0;top:1732px;width:550px;height:200px;background:var(--sage)}
.cta{left:102px;top:1765px;width:347px;height:44px;background:var(--white)}
.cta p{position:absolute;left:14px;top:15px;font-size:11px;color:var(--ink)}
.cta .btn{position:absolute;left:262px;top:16px;width:70px;height:12px;background:var(--blue);color:var(--white);font-size:3.8px;font-weight:600;display:flex;align-items:center;justify-content:center}
.col{top:1826px;width:80px}
.col h4{font-size:6.6px;font-weight:400;color:var(--ink)}
.col .dash{width:4px;height:1px;background:var(--green);margin:3px 0 6px}
.col li{list-style:none;font-size:3.6px;color:var(--muted);height:14.5px;border-bottom:1px solid #d5dccd;padding-top:3px}
.contact li{border:0;height:9px;padding:0;display:flex;align-items:center;gap:3px}
.social{left:102px;top:1877px;display:flex;gap:3px}
.social i{width:11px;height:11px;border-radius:50%;border:1px solid var(--green)}
.foot-brand{left:365px;top:1879px;display:flex;align-items:center;gap:4px}
.foot-brand .mark{width:19px;height:19px;background:var(--green)}
.foot-brand .name{font-size:13px;font-weight:700;color:var(--forest);line-height:12px}
.foot-brand .name small{display:block;font-size:7px;line-height:9px;letter-spacing:1.8px}
</style>
</head>
<body>
<div class="stage">
<main class="page">

  <section class="photo hero" role="img" aria-label="Sunlit pine forest with rays through the trees"></section>
  <div class="abs hero-glow"></div>

  <header class="abs nav">
    <div class="brand"><span class="brand-mark"></span><span class="brand-name">VERDELL<small>TREE CARE</small></span></div>
    <span class="nav-links" style="left:126px">About Us</span>
    <span class="nav-links" style="left:174px">Services</span>
    <span class="nav-links" style="left:218px">Charity</span>
    <span class="nav-links" style="left:259px">Career</span>
    <span class="nav-links" style="left:302px">Contact</span>
    <span class="nav-cta">Get a Free Quote</span>
  </header>

  <h1 class="abs hero-title">CALL <span class="accent">VERDELL</span> FOR<br>ALL YOUR TREE CARE NEEDS</h1>
  <p class="abs hero-sub">SERVING MAPLEWOOD AND SURROUNDING AREAS</p>

  <section class="abs who">
    <h2 class="abs h-who">Who We Are</h2>
    <div class="abs who-text">
      <p>At Verdell Tree Care, we are more than just a tree service company, we are stewards of our beautiful trees. With a passion deeply rooted in arboriculture, we embark on a mission to promote the health, beauty, and safety of your trees and landscapes.</p>
      <p>Whether it's expert tree trimming to enhance aesthetics, meticulous tree removal to mitigate hazards, or comprehensive tree health assessments to ensure safety, we approach each task with unwavering dedication and attention to detail.</p>
    </div>
    <div class="abs estimate">
      <p class="lead">TXT or CALL for a free estimate</p>
      <p class="phone" style="margin-top:3px">
        <svg width="6" height="9" viewBox="0 0 6 9"><rect x="0.5" y="0.5" width="5" height="8" rx="1" fill="none" stroke="#888" stroke-width="0.8"/></svg>
        (555) 214-0387</p>
      <p class="phone">(555) 630-1942</p>
    </div>
    <div class="abs who-rule"></div>
    <h3 class="abs h-do">What we do</h3>

    <article class="abs svc" style="left:46px">
      <div class="img" role="img" aria-label="Hands pruning a branch with shears" style="background:linear-gradient(135deg,#5f7a3a,#a9b98a 55%,#3e5a28)"></div>
      <h3>TREE PRUNING</h3>
      <p>Careful cuts that shape the crown, remove dead limbs and help each tree grow strong and healthy through every season of the year.</p>
      <span class="more">Full List</span>
    </article>
    <article class="abs svc" style="left:165px">
      <div class="img" role="img" aria-label="Arborist cutting into a large trunk" style="background:linear-gradient(135deg,#8a7a3a,#c2a060 50%,#6a5a2a)"></div>
      <h3>TREE REMOVAL</h3>
      <p>Safe removal of hazardous or unwanted trees by trained crews, with full cleanup of wood and debris once the work on site is done.</p>
      <span class="more">Full List</span>
    </article>
    <article class="abs svc" style="left:285px">
      <div class="img" role="img" aria-label="Avenue of tall green trees" style="background:linear-gradient(180deg,#cfe0b8,#5f8a3a 45%,#3a6a22)"></div>
      <h3>TREE PRESERVATION</h3>
      <p>Health checks, soil care and protection plans that keep mature trees thriving during building work and long after it ends.</p>
      <span class="more">Full List</span>
    </article>

    <div class="abs perks">
      <div class="abs perk" style="left:46px">
        <svg width="16" height="16" viewBox="0 0 16 16" fill="none" stroke="#fff" stroke-width="0.9"><circle cx="6" cy="4" r="2.5"/><path d="M1 15v-4a5 5 0 0 1 10 0v4M11 9h4v6h-4z"/></svg>
        <div><b>Licensed Professionals</b><span>Certified and insured crews</span></div>
      </div>
      <div class="abs perk" style="left:166px">
        <svg width="16" height="16" viewBox="0 0 16 16" fill="none" stroke="#fff" stroke-width="0.9"><rect x="1" y="3" width="14" height="11" rx="1"/><path d="M1 6h14M4 1v4M12 1v4M4 9h3M4 11h5"/></svg>
        <div><b>Online Service Booking</b><span>Pick a time that suits you</span></div>
      </div>
      <div class="abs perk" style="left:286px">
        <svg width="16" height="16" viewBox="0 0 16 16" fill="none" stroke="#fff" stroke-width="0.9"><rect x="1" y="4" width="14" height="11" rx="1"/><path d="M4 4V2h8v2M5 10l2 2 4-4"/></svg>
        <div><b>Premium Grass &amp; Plant Seeds</b><span>We cover all aspects of tree work</span></div>
      </div>
    </div>
  </section>

  <p class="abs kicker">Our Expertise</p>
  <div class="abs kicker-dash"></div>
  <h2 class="abs h-exp">Thoughtful improvements to enrich your <em>residential</em> or <em>corporate</em> appearance</h2>
  <ul class="abs checks">
    <li><svg width="5" height="5" viewBox="0 0 5 5"><path d="M0.5 2.6l1.4 1.4L4.5 1" stroke="#28b93a" stroke-width="1" fill="none"/></svg>5 Year Warranty on Workmanship</li>
    <li><svg width="5" height="5" viewBox="0 0 5 5"><path d="M0.5 2.6l1.4 1.4L4.5 1" stroke="#28b93a" stroke-width="1" fill="none"/></svg>Every Project is Run by a Team of Experts</li>
    <li><svg width="5" height="5" viewBox="0 0 5 5"><path d="M0.5 2.6l1.4 1.4L4.5 1" stroke="#28b93a" stroke-width="1" fill="none"/></svg>We Save You Time, Money, and Space</li>
  </ul>
  <div class="photo video" role="img" aria-label="Modern house with lawn, pond and lit brick wall at dusk">
    <div class="play"><svg width="15" height="15" viewBox="0 0 15 15"><path d="M6 4.5l4.5 3-4.5 3z" fill="#fff"/></svg></div>
  </div>

  <div class="photo svc-hero" role="img" aria-label="Gardener in green apron holding hedge trimmer">
    <span class="label">Services</span>
    <span class="sub">Cost Calculator</span>
  </div>
  <div class="abs tile" style="left:280px;top:750px">
    <svg width="26" height="24" viewBox="0 0 26 24" fill="none" stroke="#28b93a" stroke-width="1"><path d="M4 14c4-2 8-2 10 1M14 15l6-4M3 20h20M6 20v-3M10 20v-4M14 20v-3M18 20v-4"/><circle cx="17" cy="6" r="4"/></svg>
    <span>Grass Installation</span>
  </div>
  <div class="abs tile" style="left:368px;top:750px">
    <svg width="26" height="24" viewBox="0 0 26 24" fill="none" stroke="#28b93a" stroke-width="1"><circle cx="11" cy="8" r="6"/><path d="M11 14v8M4 22h18M18 12h5v6h-5z"/></svg>
    <span>Landscape Lighting</span>
  </div>
  <div class="abs tile" style="left:280px;top:837px">
    <svg width="26" height="24" viewBox="0 0 26 24" fill="none" stroke="#28b93a" stroke-width="1"><path d="M5 4l6 6M21 4l-6 6M8 14c0-4 10-4 10 0v6H8zM3 22h20"/></svg>
    <span>Hardscaping</span>
  </div>
  <div class="abs tile" style="left:368px;top:837px">
    <svg width="26" height="24" viewBox="0 0 26 24" fill="none" stroke="#28b93a" stroke-width="1"><circle cx="9" cy="15" r="6"/><circle cx="18" cy="10" r="5"/><path d="M13 2v6M3 22h20"/></svg>
    <span>Landscaping</span>
  </div>

  <div class="abs work-band"></div>
  <h2 class="abs h-work">Our Most Recent Work</h2>
  <p class="abs work-text">Whether it is a courtyard or large space, we can design, landscape or maintain your garden to the highest standard. We use only the best materials. We aim to create a garden that you can enjoy whatever your specification to achieve a unique space.</p>
  <div class="photo before" role="img" aria-label="Garden lawn before landscaping"></div>
  <div class="photo after" role="img" aria-label="Garden with curving lawn and flower borders after landscaping"></div>
  <div class="abs slider">&lsaquo;&rsaquo;</div>

  <div class="photo thumb" role="img" aria-label="Garden path with clipped hedges" style="left:100px;top:1277px;background:linear-gradient(180deg,#4f7a2a,#8aa86a 60%,#3e6a22)"></div>
  <div class="photo thumb" role="img" aria-label="Formal garden with colourful flower beds" style="left:191px;top:1277px;background:linear-gradient(180deg,#3e6a22,#c07a8a 50%,#5a8a3a)"></div>
  <div class="photo thumb" role="img" aria-label="House front with lawn and shrubs" style="left:100px;top:1367px;background:linear-gradient(180deg,#b8a890,#7a9a5a 55%,#4f8a2a)"></div>
  <div class="photo thumb" role="img" aria-label="Garden with fountain and topiary" style="left:191px;top:1367px;background:linear-gradient(180deg,#4a7a2a,#8ab05a 50%,#b86aa0)"></div>
  <div class="photo projects" role="img" aria-label="Modern house with lit windows and garden at dusk">
    <span class="label">Projects</span>
    <span class="sub">All Projects</span>
  </div>

  <section class="abs quote"></section>
  <div class="photo quote-photo" role="img" aria-label="Gardener in orange cap working among flowers"></div>
  <h2 class="abs h-quote">Get a Free Estimate</h2>
  <p class="abs form-label" style="left:102px">Your Info</p>
  <p class="abs form-label" style="left:236px">Services Needed</p>
  <div class="abs field" style="top:1588px">Name</div>
  <div class="abs field" style="top:1605px">Phone</div>
  <div class="abs field" style="top:1623px">Address</div>
  <div class="abs field" style="top:1641px">Email</div>
  <div class="abs opt" style="top:1587px"><i></i>Lawn Care</div>
  <div class="abs opt" style="top:1598px"><i></i>Landscaping</div>
  <div class="abs opt" style="top:1609px"><i></i>Leaf Removal</div>
  <div class="abs opt" style="top:1620px"><i></i>Snow Removal</div>
  <div class="abs submit">SUBMIT REQUEST</div>

  <footer class="abs footer"></footer>
  <div class="abs cta"><p>Contact us now to get quote</p><span class="btn">Give me free quote</span></div>

  <div class="abs col contact" style="left:102px">
    <h4>Contact Us</h4><div class="dash"></div>
    <ul>
      <li><svg width="4" height="4" viewBox="0 0 4 4"><path d="M0.5 0.5h1l0.5 1-0.6 0.5a2 2 0 0 0 1 1l0.5-0.6 1 0.5v1A3 3 0 0 1 0.5 0.5z" fill="#28b93a"/></svg>1-123-456-789</li>
      <li><svg width="4" height="4" viewBox="0 0 4 4"><rect y="0.7" width="4" height="2.8" fill="#28b93a"/></svg>info@example.com</li>
      <li><svg width="4" height="4" viewBox="0 0 4 4"><path d="M2 4L0.6 1.8a1.4 1.4 0 1 1 2.8 0z" fill="#28b93a"/></svg>Your address goes here ...</li>
    </ul>
  </div>
  <div class="abs social"><i></i><i></i><i></i></div>
  <div class="abs col" style="left:191px;width:78px">
    <h4>About Us</h4><div class="dash"></div>
    <ul><li>Home</li><li>About</li><li>Blog</li><li>Contact</li></ul>
  </div>
  <div class="abs col" style="left:281px;width:78px">
    <h4>Popular Services</h4><div class="dash"></div>
    <ul><li>Landscaping</li><li>Hardscaping</li><li>Irrigation</li><li>Landscape Design</li></ul>
  </div>
  <div class="abs col contact" style="left:370px">
    <h4>Emergency Service</h4><div class="dash"></div>
    <ul><li><svg width="6" height="9" viewBox="0 0 6 9"><rect x="0.5" y="0.5" width="5" height="8" rx="1" fill="none" stroke="#28b93a" stroke-width="0.8"/></svg>&nbsp;1-123-456-789</li></ul>
  </div>
  <div class="abs foot-brand"><span class="mark"></span><span class="name">VERDELL<small>TREE CARE</small></span></div>

</main>
</div>
</body>
</html>
```